Online business manager needs a website

I need a website designed and then coded. I am an online business manager serving a number of different industries providing administrative support to existing small businesses and helping solo practitioners get their new business up and running.

I didn't have a logo formally designed but have been using the attached avatar and wouldn't mind something that incorporated that.

The business doesn't have an official name, so I've just been using my name Lena Morvath, Online Business Manager or Lena Morvath, OBM. I've attached two documents that I have made previously for an example of content.

I would prefer the final site be in Wordpress.

Requirements
Must have
• A way to contact me, testimonials, list of services

```html
<!DOCTYPE html>
<html lang="en">
<head>
<meta charset="utf-8">
<title>Lena Morvath – Online Business Manager</title>
<link rel="stylesheet" href="https://fonts.googleapis.com/css2?family=Barlow:wght@400;500;600;700;800&display=swap">
<style>
:root{
  --purple:#4b1c82;
  --purple-deep:#2e0b57;
  --purple-mid:#6a3aa6;
  --ink:#222;
  --muted:#666;
  --grey-bg:#f2f2f2;
  --white:#fff;
}
*{margin:0;padding:0;box-sizing:border-box}
html,body{width:1200px;height:3705px;overflow:hidden}
body{font-family:"Barlow",sans-serif;color:var(--ink);background:var(--white);position:relative}
.abs{position:absolute}
/* header */
.site-header{position:absolute;top:0;left:0;width:1200px;height:76px;background:var(--white);z-index:5}
.brand{position:absolute;left:110px;top:16px}
.brand-name{font-size:25px;font-weight:600;color:#333;line-height:1}
.brand-tag{font-size:13px;color:#777;margin-top:4px}
.main-nav{position:absolute;left:427px;top:34px;display:flex;gap:29px;font-size:14px;font-weight:600;color:#333}
.main-nav .active{color:var(--purple)}
.nav-marker{position:absolute;left:437px;top:0;width:0;height:0;border-left:9px solid transparent;border-right:9px solid transparent;border-top:14px solid var(--purple)}
.call{position:absolute;left:913px;top:18px;display:flex;align-items:center;gap:14px}
.icon-circle{width:32px;height:32px;border-radius:50%;background:var(--purple);display:flex;align-items:center;justify-content:center}
.call-label{font-size:13px;color:#777}
.call-num{font-size:21px;font-weight:700;color:#333;line-height:1.1}
/* hero */
.hero{position:absolute;top:76px;left:0;width:1200px;height:744px;overflow:hidden}
.hero-photo{position:absolute;inset:0;background:linear-gradient(100deg,#a58fc9 0%,#9d88bf 35%,#6d6a78 55%,#3e3b42 75%,#2b2a30 100%)}
.hero-title{position:absolute;left:108px;top:218px;font-size:86px;font-weight:700;color:var(--white);line-height:1;letter-spacing:-1px}
.hero-sub{position:absolute;left:110px;top:318px;font-size:26px;font-weight:600;color:var(--white)}
.btn{display:inline-flex;align-items:center;justify-content:center;border-radius:26px;background:var(--purple);color:var(--white);font-size:14px;font-weight:700;text-transform:uppercase}
.hero .btn{position:absolute;left:107px;top:362px;width:171px;height:48px}
.hero-wave{position:absolute;left:0;bottom:0}
/* about */
.about-photo{left:153px;top:861px;width:398px;height:398px;border-radius:50%;background:radial-gradient(circle at 50% 50%,#c08a7a 0%,#8b3a62 55%,#3e4a2e 100%)}
.about-title{left:623px;top:912px;font-size:43px;font-weight:700;color:#222}
.about-text{left:623px;top:979px;width:466px;font-size:12.5px;line-height:21.5px;color:#666;text-align:justify}
.about .btn{position:absolute;left:622px;top:1172px;width:171px;height:48px}
/* services */
.services{position:absolute;top:1321px;left:0;width:1200px;height:616px;background:var(--grey-bg)}
.section-title{position:absolute;left:0;width:1200px;text-align:center;font-size:42px;font-weight:700;color:#222}
.service-card{position:absolute;top:168px;width:230px;height:349px;background:var(--white);box-shadow:0 2px 10px rgba(0,0,0,.08)}
.service-img{position:absolute;left:11px;top:12px;width:209px;height:165px}
.service-card h3{position:absolute;left:26px;top:195px;font-size:21px;font-weight:600;line-height:22px;color:#222}
.ticks{position:absolute;left:25px;top:256px;list-style:none;font-size:13px;color:#666}
.ticks li{display:flex;align-items:center;gap:10px;height:21.5px}
.ticks li::before{content:"✓";width:12px;height:12px;border-radius:50%;background:var(--purple);color:#fff;font-size:8px;font-weight:700;display:flex;align-items:center;justify-content:center;flex:none}
/* testimonials */
.testimonials{position:absolute;top:1937px;left:0;width:1200px;height:574px;background:linear-gradient(180deg,#8a5cc0 0%,#5d2a98 35%,#3c1172 70%,#2b0853 100%);overflow:hidden}
.testimonials .section-title{color:var(--white);top:95px}
.slider-bar{position:absolute;left:196px;top:331px;width:804px;height:46px;border-radius:23px;background:rgba(255,255,255,.35);color:#fff;font-size:18px}
.slider-bar span{position:absolute;top:11px}
.quote-card{position:absolute;left:262px;top:217px;width:676px;height:252px;background:var(--white);border-radius:3px;text-align:center}
.quote-text{position:absolute;left:35px;top:50px;width:606px;font-size:16px;line-height:26px;color:#555}
.quote-mark{position:absolute;font-size:80px;color:#ececec;font-family:Georgia,serif;line-height:1}
.quote-name{position:absolute;left:0;width:676px;top:165px;font-size:16px;font-weight:600;color:#333}
.quote-role{position:absolute;left:0;width:676px;top:193px;font-size:16px;color:#666}
.avatar{position:absolute;left:536px;top:156px;width:108px;height:108px;border-radius:50%;border:4px solid #fff;background:linear-gradient(135deg,#c98b5a,#7a4a2c)}
/* rates */
.rates .section-title{top:2603px}
.rate-card{position:absolute;top:2697px;width:225px;background:var(--white);box-shadow:0 2px 12px rgba(0,0,0,.09);text-align:center;color:#555}
.rate-card.featured{background:var(--purple);color:#fff}
.price{margin:30px auto 0;width:106px;height:106px;border-radius:50%;background:var(--purple);color:#fff;font-size:33px;font-weight:700;display:flex;align-items:center;justify-content:center}
.featured .price{background:#fff;color:var(--purple)}
.rate-card h4{margin-top:16px;font-size:21px;font-weight:700;color:var(--purple)}
.featured h4{color:#fff}
.rate-list{list-style:none;text-align:left;padding-left:40px;margin-top:14px;font-size:14px}
.rate-list li{height:28.5px;display:flex;align-items:center;gap:14px}
.rate-list li::before{content:"✓";color:var(--purple);font-weight:700;font-size:14px}
.featured .rate-list li::before{color:#fff}
.response{margin-top:17px;font-size:14px;padding-bottom:28px}
.rates .btn.pill{position:absolute;left:388px;top:3028px;width:172px;height:48px;background:var(--purple-deep);border:3px solid var(--purple-mid)}
/* footer */
.site-footer{position:absolute;top:3166px;left:0;width:1200px;height:539px;color:#fff}
.footer-bg{position:absolute;left:0;top:0}
.footer-title{position:absolute;left:0;width:1200px;top:148px;text-align:center;font-size:35px;font-weight:700}
.footer-sub{position:absolute;left:0;width:1200px;top:189px;text-align:center;font-size:18px}
.footer-nav{position:absolute;left:0;width:1200px;top:232px;text-align:center;font-size:17px}
.footer-nav span{margin:0 14px}
.contact-item{position:absolute;top:300px;display:flex;gap:16px;font-size:14px;line-height:26px}
.contact-item .icon-circle{background:#fff;width:34px;height:34px;margin-top:6px}
.footer-rule{position:absolute;left:220px;top:401px;width:760px;height:3px;background:linear-gradient(90deg,transparent,rgba(255,255,255,.6),transparent)}
.copyright{position:absolute;left:0;width:1200px;top:436px;text-align:center;font-size:14px}
.social{position:absolute;left:557px;top:470px;display:flex;gap:5px}
.social span{width:26px;height:26px;border-radius:50%;background:#fff}
</style>
</head>
<body>

<header class="site-header">
  <div class="nav-marker"></div>
  <div class="brand">
    <div class="brand-name">Lena Morvath</div>
    <div class="brand-tag">Online Business Manager</div>
  </div>
  <nav class="main-nav">
    <span class="active">Home</span><span>About Me</span><span>Services</span><span>Testimonials</span><span>Contact Me</span>
  </nav>
  <div class="call">
    <div class="icon-circle"><svg width="14" height="14" viewBox="0 0 24 24"><path fill="#fff" d="M6.6 10.8a15.1 15.1 0 0 0 6.6 6.6l2.2-2.2c.3-.3.7-.4 1-.2 1.1.4 2.3.6 3.6.6.6 0 1 .4 1 1V20c0 .6-.4 1-1 1A17 17 0 0 1 3 4c0-.6.4-1 1-1h3.5c.6 0 1 .4 1 1 0 1.3.2 2.5.6 3.6.1.3 0 .7-.2 1z"/></svg></div>
    <div><div class="call-label">Call Us :</div><div class="call-num">555.014.2290</div></div>
  </div>
</header>

<section class="hero">
  <div class="hero-photo" role="img" aria-label="Two colleagues looking at a tablet together in an office"></div>
  <h1 class="hero-title">Lena Morvath</h1>
  <div class="hero-sub">Virtual Assistant</div>
  <a class="btn">Get Started</a>
  <svg class="hero-wave" width="1200" height="744" viewBox="0 0 1200 744">
    <path fill="#fff" d="M0 680 C120 620 260 596 420 630 C560 660 640 742 800 744 C960 746 1100 690 1200 660 L1200 744 L0 744Z"/>
    <path fill="#4b1c82" d="M0 672 C120 608 260 584 420 618 C560 648 640 730 800 732 C960 734 1100 678 1200 646 L1200 660 C1100 690 960 746 800 744 C640 742 560 660 420 630 C260 596 120 620 0 680Z"/>
    <rect x="576" y="636" width="50" height="66" rx="25" fill="#fff"/>
    <rect x="590" y="654" width="22" height="32" rx="11" fill="none" stroke="#333" stroke-width="2"/>
    <line x1="601" y1="660" x2="601" y2="668" stroke="#333" stroke-width="2"/>
    <path d="M588 698 L601 708 L614 698 M588 708 L601 718 L614 708" fill="none" stroke="#222" stroke-width="3"/>
  </svg>
</section>

<section class="about">
  <div class="abs about-photo" role="img" aria-label="Portrait of Lena Morvath in front of a flowering bush"></div>
  <h2 class="abs about-title">About Me</h2>
  <p class="abs about-text">Hi! I'm so excited that you have chosen to explore my portfolio. Helping businesses achieve their goals is my passion, and I'm thrilled that with my assistance you will have more time for your own passion project. I thrive while working independently, which means you can be confident when leaving tasks for me. The type of work that lights me up is anything involving organization and/or spreadsheets. You need data analyzed that includes multiple nested if formulas? You have an overwhelming amount of email to sort through and appointments to book? I'm your gal!</p>
  <a class="btn">Learn More</a>
</section>

<section class="services">
  <h2 class="section-title" style="top:88px">Our Services</h2>
  <article class="service-card" style="left:111px">
    <div class="service-img" role="img" aria-label="Laptop on a desk beside a calendar" style="background:linear-gradient(135deg,#b9bec4,#6f7780)"></div>
    <h3>Virtual<br>Assistance</h3>
    <ul class="ticks"><li>Calendar Management</li><li>Email Management</li><li>Light Graphic Design</li><li>Data Entry</li></ul>
  </article>
  <article class="service-card" style="left:360px">
    <div class="service-img" role="img" aria-label="Typewritten page beside a green plant" style="background:linear-gradient(90deg,#3f5a28,#d8d4c8 45%,#ece9e0)"></div>
    <h3>Social Media &amp;<br>Content Management</h3>
    <ul class="ticks"><li>Content Repurposing</li><li>Graphics Creation</li><li>Audiogram Creation</li><li>Search Engine Optimization</li></ul>
  </article>
  <article class="service-card" style="left:609px">
    <div class="service-img" role="img" aria-label="Calculator, keyboard and financial papers on a blue desk" style="background:linear-gradient(135deg,#8ec6dc,#d7e6ec 50%,#7fb9d0)"></div>
    <h3>Finance<br>Management</h3>
    <ul class="ticks"><li>Create Invoices</li><li>Track Receivables</li><li>Analyze Expenses</li><li>Year Over Year Analytics</li></ul>
  </article>
  <article class="service-card" style="left:858px">
    <div class="service-img" role="img" aria-label="Businesswoman at a desk in front of a sticky-note wall" style="background:linear-gradient(135deg,#e88aa0,#b9d4d8 50%,#6e6a6c)"></div>
    <h3>Business<br>Management</h3>
    <ul class="ticks"><li>Creation of Operating</li><li>Review of Website Strategy</li><li>Reporting and Analytics</li><li>Project Management</li></ul>
  </article>
</section>

<section class="testimonials">
  <h2 class="section-title">Testimonials</h2>
  <div class="slider-bar"><span style="left:32px">‹</span><span style="right:32px">›</span></div>
  <div class="quote-card">
    <span class="quote-mark" style="left:30px;top:30px">“</span>
    <span class="quote-mark" style="right:32px;top:92px">”</span>
    <p class="quote-text">When it became apparent that a project would take more time than I had, Lena stepped up to take on the required research. She was thorough and timely; able to meet a last-minute 12-hour deadline. I would highly recommend Lena to assist with your next project.</p>
    <div class="quote-name">Dana R.</div>
    <div class="quote-role">Owner, Ridgeline Roofing</div>
  </div>
  <div class="avatar" role="img" aria-label="Portrait of the client giving the testimonial"></div>
</section>

<section class="rates">
  <h2 class="section-title">Rates And Packages</h2>
  <div class="rate-card" style="left:112px">
    <div class="price">$40</div><h4>Hourly Rate</h4>
    <ul class="rate-list"><li>For clients</li><li>needing only</li><li>occasional help</li></ul>
    <div style="height:30px"></div>
  </div>
  <div class="rate-card featured" style="left:361px;height:351px">
    <div class="price">$700</div><h4>20 hours/month</h4>
    <ul class="rate-list"><li>Includes one 15</li><li>minute meeting</li><li>per week</li></ul>
    <div class="response">Responses within 72 hours</div>
  </div>
  <div class="rate-card" style="left:613px">
    <div class="price" style="font-size:28px">$1,300</div><h4>40 hours/month</h4>
    <ul class="rate-list"><li>Includes one 30</li><li>minute meeting</li><li>per week</li></ul>
    <div class="response">Responses within 72 hours</div>
  </div>
  <div class="rate-card" style="left:863px">
    <div class="price" style="font-size:28px">$2,400</div><h4>80 hours/month</h4>
    <ul class="rate-list"><li>Includes one 60</li><li>minute meeting</li><li>per week</li></ul>
    <div class="response">Responses within 72 hours</div>
  </div>
  <a class="btn pill">Learn More</a>
</section>

<footer class="site-footer">
  <svg class="footer-bg" width="1200" height="539" viewBox="0 0 1200 539">
    <defs><linearGradient id="footGrad" x1="0" y1="0" x2="0" y2="1"><stop offset="0" stop-color="#3a0f6e"/><stop offset="1" stop-color="#3d1377"/></linearGradient></defs>
    <path fill="#4b1c82" d="M0 80 C150 30 320 10 520 50 C720 90 820 150 1000 120 C1100 105 1160 80 1200 70 L1200 539 L0 539Z"/>
    <path fill="url(#footGrad)" d="M0 102 C150 52 320 32 520 72 C720 112 820 172 1000 142 C1100 127 1160 102 1200 92 L1200 539 L0 539Z"/>
  </svg>
  <div class="footer-title">LENA MORVATH</div>
  <div class="footer-sub">Online Business Manager</div>
  <div class="footer-nav">Home<span>|</span>About Me<span>|</span>Services<span>|</span>Pricing<span>|</span>Contact</div>
  <div class="contact-item" style="left:219px">
    <div class="icon-circle"><svg width="12" height="16" viewBox="0 0 12 16"><path fill="#4b1c82" d="M6 0a6 6 0 0 0-6 6c0 4.5 6 10 6 10s6-5.5 6-10a6 6 0 0 0-6-6zm0 8.5A2.5 2.5 0 1 1 6 3.5a2.5 2.5 0 0 1 0 5z"/></svg></div>
    <div>123, Lorem ipsum dolor sit<br>amet, consectetur</div>
  </div>
  <div class="contact-item" style="left:520px">
    <div class="icon-circle"><svg width="14" height="14" viewBox="0 0 24 24"><path fill="#4b1c82" d="M6.6 10.8a15.1 15.1 0 0 0 6.6 6.6l2.2-2.2c.3-.3.7-.4 1-.2 1.1.4 2.3.6 3.6.6.6 0 1 .4 1 1V20c0 .6-.4 1-1 1A17 17 0 0 1 3 4c0-.6.4-1 1-1h3.5c.6 0 1 .4 1 1 0 1.3.2 2.5.6 3.6.1.3 0 .7-.2 1z"/></svg></div>
    <div>Phone :<br>555.014.2290</div>
  </div>
  <div class="contact-item" style="left:751px">
    <div class="icon-circle"><svg width="14" height="11" viewBox="0 0 14 11"><rect width="14" height="11" rx="1.5" fill="#4b1c82"/><path d="M1 1.5 L7 6 L13 1.5" fill="none" stroke="#fff" stroke-width="1.3"/></svg></div>
    <div>Email :<br>hello@lenamorvath.com</div>
  </div>
  <div class="footer-rule"></div>
  <div class="copyright">Copyright © 2023 Company name | Privacy Policy | Terms &amp; Conditions</div>
  <div class="social"><span></span><span></span><span></span></div>
</footer>

</body>
</html>
```